Brightway Haus Inc. Business Card Design

Brightway Haus Inc. is in search of a great clean design for our business cards!

Looking to incorporate our full logo and watermark on side one (however, I am open to having the text and watermark separated within the design.)

On side two, I am looking to have contact information (Name, Position, Phone #, Email, Website (www.thebrightwayhaus.ca). Can have the logo and/or watermark as part of the design if applicable.

Please add tagline "Where Shine Counts" on either side 1 or 2. This tagline can be in a sans serif, serif or cursive font as long as it compliments overall design. Capitalization can be title or sentence case depending on how it fits within the design.

Get creative!! Looking for a clean, crisp, premium design! Looking for a glossy card finish with spot UV features when printed. Cards will also be printed with rounded corners. Standard dimensions (3.5 x 2).

Target Market(s)

B2B - primary clients are business owners or property management corporations. (residential jobs are few and far between)

Industry/Entity Type

Business

Contact Information for Business Card

- clean, crisp design
- double sided
- spot UV accents and glossy finish upon printing
- standard business card size (3.5 x 2) with rounded corners
- please see project description for requirements per side

Font styles to use
Sans Serif

Requirements
Must have
• - adequate bleeds with print ready files
• - cohesive design elements between side 1 & 2
• - spot UV elements (can be on both sides or just one, use your discretion)
• - colour pallet should match the logo file provided
• - incorporate tagline "where shine counts" (this tagline can be in a serif or sans serif font as long as it is complimentary to the overall design.
Nice to have
• - Premium elements with a clean design
Should not have
• - Please omit cartoon or whimsical like designs, think premium.
• - Colours should not stray from the pallet of the provided logo.

```html
<!DOCTYPE html>
<html lang="en">
<head>
<meta charset="utf-8">
<title>Brightway Haus Inc. Business Card</title>
<link rel="stylesheet" href="https://fonts.googleapis.com/css2?family=Roboto:ital,wght@0,400;0,700;1,400&family=Roboto+Condensed:wght@400;700&display=swap">
<style>
  :root {
    --stage: #2b2b2d;
    --paper: #f2f2f2;
    --teal: #13b2b4;
    --navy: #1b2550;
    --grey: #a9aaad;
    --white: #ffffff;
  }
  * { margin: 0; padding: 0; box-sizing: border-box; }
  html, body { width: 1200px; height: 960px; overflow: hidden; }
  body {
    background: var(--stage);
    position: relative;
    font-family: "Roboto", Arial, sans-serif;
  }
  .card {
    position: absolute;
    width: 600px;
    height: 343px;
    border-radius: 22px;
    overflow: hidden;
  }
  .card--front { left: 314px; top: 113px; background: var(--paper); }
  .card--back  { left: 311px; top: 472px; height: 342px; background: var(--navy); }

  .front-swoosh { position: absolute; inset: 0; }

  .brand {
    position: absolute;
    display: flex;
    align-items: center;
    gap: 10px;
    font-family: "Roboto", Arial, sans-serif;
    font-weight: 700;
    white-space: nowrap;
    letter-spacing: 0.2px;
  }
  .brand__mark { display: block; }
  .brand--front { left: 44px; top: 50px; font-size: 27px; color: var(--navy); }
  .brand--front .brand__mark { width: 26px; height: 26px; background: var(--teal); }
  .brand--back {
    left: 0; right: 0; top: 146px; justify-content: center;
    font-size: 38px; color: var(--white); gap: 14px;
  }
  .brand--back .brand__mark { width: 36px; height: 36px; background: var(--teal); }

  .holder {
    position: absolute; right: 33px; top: 44px; text-align: right;
    font-family: "Roboto Condensed", Arial, sans-serif; color: var(--white);
  }
  .holder__name { font-size: 21px; font-weight: 700; line-height: 26px; }
  .holder__role { font-size: 15px; font-weight: 400; line-height: 20px; letter-spacing: 0.3px; }

  .address {
    position: absolute; right: 33px; top: 170px; text-align: right;
    color: var(--white); font-size: 14px; line-height: 19px;
  }
  .contacts {
    position: absolute; right: 27px; top: 217px; list-style: none;
    color: var(--white); font-size: 14px; line-height: 19.2px;
  }
  .contacts li { display: flex; justify-content: flex-end; align-items: center; gap: 7px; }
  .contacts svg { width: 13px; height: 13px; flex: none; }

  .tagline {
    position: absolute; left: 0; right: 0; top: 276px;
    display: flex; align-items: center; justify-content: center; gap: 4px;
    font-style: italic; font-size: 19px; color: var(--white);
  }
  .tagline__rule { width: 116px; height: 1px; }
  .tagline__rule--left  { background: linear-gradient(to right, transparent, rgba(255,255,255,.9)); }
  .tagline__rule--right { background: linear-gradient(to left, transparent, rgba(255,255,255,.9)); }
  .tagline__accent { color: var(--teal); }
</style>
</head>
<body>

<section class="card card--front" aria-label="Business card front">
  <svg class="front-swoosh" viewBox="0 0 600 343" width="600" height="343" aria-hidden="true">
    <path fill="var(--grey)" d="M300 0 C385 0 386 75 350 140 C310 215 230 285 160 343 L600 343 L600 0 Z"/>
    <path fill="var(--navy)" d="M318 0 C402 2 404 78 366 146 C325 220 242 290 168 343 L600 343 L600 0 Z"/>
    <path fill="var(--teal)" stroke="var(--white)" stroke-width="1.5"
          d="M338 0 C398 14 394 96 358 164 C318 238 246 296 176 343 L600 343 L600 0 Z"/>
  </svg>

  <div class="brand brand--front">
    <span class="brand__mark"></span>
    <span class="brand__name">BRIGHTWAY HAUS INC.</span>
  </div>

  <div class="holder">
    <p class="holder__name">MARCUS HALE</p>
    <p class="holder__role">CEO/FOUNDER</p>
  </div>

  <address class="address" style="font-style:normal">
    214 Larkspur Avenue<br>
    Halifax, Nova Scotia 30412
  </address>

  <ul class="contacts">
    <li>555 214 3071
      <svg viewBox="0 0 24 24" aria-hidden="true"><path fill="#fff" d="M6.6 10.8a15.1 15.1 0 0 0 6.6 6.6l2.2-2.2c.3-.3.7-.4 1-.2 1.1.4 2.3.6 3.6.6.6 0 1 .4 1 1V20c0 .6-.4 1-1 1A17 17 0 0 1 3 4c0-.6.4-1 1-1h3.5c.6 0 1 .4 1 1 0 1.3.2 2.5.6 3.6.1.3 0 .7-.2 1z"/></svg>
    </li>
    <li>555 386 9152
      <svg viewBox="0 0 24 24" aria-hidden="true"><rect x="6" y="1.5" width="12" height="21" rx="2" fill="none" stroke="#fff" stroke-width="2"/><circle cx="12" cy="19" r="1.2" fill="#fff"/></svg>
    </li>
    <li>555 720 4468
      <svg viewBox="0 0 24 24" aria-hidden="true"><rect x="6" y="2" width="12" height="6" fill="#fff"/><rect x="2" y="9" width="20" height="9" rx="1.5" fill="#fff"/><rect x="6" y="15" width="12" height="7" fill="#fff" stroke="var(--teal)" stroke-width="1.2"/></svg>
    </li>
    <li>hello@brightwayhaus.ca
      <svg viewBox="0 0 24 24" aria-hidden="true"><rect x="2" y="5" width="20" height="14" fill="#fff"/><path d="M2 5l10 8 10-8" fill="none" stroke="var(--teal)" stroke-width="1.6"/></svg>
    </li>
    <li>www.thebrightwayhaus.ca
      <svg viewBox="0 0 24 24" aria-hidden="true"><circle cx="12" cy="12" r="10" fill="#fff"/><path d="M12 2c-3 3-3 17 0 20M12 2c3 3 3 17 0 20M2 12h20" fill="none" stroke="var(--teal)" stroke-width="1.4"/></svg>
    </li>
  </ul>
</section>

<section class="card card--back" aria-label="Business card back">
  <div class="brand brand--back">
    <span class="brand__mark"></span>
    <span class="brand__name">BRIGHTWAY HAUS INC.</span>
  </div>

  <p class="tagline">
    <span class="tagline__rule tagline__rule--left"></span>
    <span>Where <span class="tagline__accent">Shine</span> Counts</span>
    <span class="tagline__rule tagline__rule--right"></span>
  </p>
</section>

</body>
</html>
```